Powerpoint design template for LUMOTEX for new digital platform

We would like to use a PowerPoint template, we would like to create a new page, we would like to create a new digital platform LUMOTEX for schools and parents for the creation of playful communication and educational tools for children to enhance their positive development, amaze them learn in a playful way. This platform is going to be the most creative, stimulating and innovative classroom, easy to use and fast to implement. Scrapbooking, collages ... Magazine, newsletters Diplomla / awards Slideshows Facebook Calendars Organizers Greetings Games ... This powerpoint template will be used essential to We are looking for a professional design, positioning our brand in the children market with an adult hearing. so you will need to find a good deal. Primary target: nurseries & schools from 0 to 18 years old and universities (in 2nd phase) Secondary target: small & medium businesses Third target: general public, and TPE If it is a color scheme, then it is suggested that it be marketed in Europe (UK, Italy, Spain) and in a 2nd Stage USA and other countries. multiple options for front page, insidious pages (multiple styles with limited text and extended text) and final contact page We need something to read, we can not do it too much, but we can not do it. , and inside pages aligned to our logo

Target Market(s)

Target 1; Education with teacher Target 2; parents and grandparents

Industry/Entity Type

Education

Font styles to use
Other font styles liked:
• not decided. but not too fancy

Requirements
Must have
• Multi page options for front page, page insides (multiple styles with limited text and extended text) and final page contact
Nice to have
• do not have a lot of ideas. We need something to read, we can not get away from it
Should not have
• not too fancy and busy: keep clarity & simplicity while reassuring on quality

```html
<!DOCTYPE html>
<html lang="en">
<head>
<meta charset="UTF-8">
<title>LUMOTEX – Project Title Slide</title>
<link rel="stylesheet" href="https://fonts.googleapis.com/css2?family=Roboto+Condensed:wght@400;700&family=Montserrat:wght@400&display=swap">
<style>
  :root {
    --lime: #d9e241;
    --lime-mid: #b7d637;
    --lime-deep: #8cc63f;
    --teal: #14b5a8;
    --ink: #111111;
    --paper: #ffffff;
  }
  * { margin: 0; padding: 0; box-sizing: border-box; }
  html, body { width: 1200px; height: 900px; overflow: hidden; background: var(--paper); }
  .slide {
    position: relative;
    width: 1200px;
    height: 900px;
    overflow: hidden;
    background: var(--paper);
    font-family: "Roboto Condensed", "Arial Narrow", sans-serif;
  }
  .slide__backdrop { position: absolute; inset: 0; width: 1200px; height: 900px; }
  .title-block { position: absolute; left: 101px; top: 288px; }
  .title-block__heading {
    font-weight: 700;
    font-size: 55px;
    line-height: 1;
    color: var(--ink);
    letter-spacing: 0.2px;
  }
  .title-block__accent { color: var(--teal); }
  .title-block__subtext {
    margin-top: 28px;
    font-weight: 400;
    font-size: 36px;
    line-height: 1;
    color: var(--ink);
  }
  .brand { position: absolute; left: 688px; top: 640px; }
  .brand__name {
    font-family: "Roboto Condensed", "Arial Narrow", sans-serif;
    font-weight: 700;
    font-size: 104px;
    line-height: 1;
    color: var(--ink);
    letter-spacing: 2px;
  }
  .brand__tagline {
    margin-top: 14px;
    font-family: "Montserrat", Arial, sans-serif;
    font-size: 20px;
    line-height: 1.25;
    letter-spacing: 5px;
    color: var(--ink);
  }
</style>
</head>
<body>
  <main class="slide">
    <svg class="slide__backdrop" viewBox="0 0 1200 900" aria-hidden="true">
      <polygon class="panel panel--deep" points="0,0 1190,0 1190,22 315,900 0,900" fill="var(--lime-deep)"/>
      <polygon class="panel panel--mid" points="0,0 1175,0 1175,12 300,900 0,900" fill="var(--lime-mid)"/>
      <polygon class="panel panel--main" points="0,0 1158,0 285,900 0,900" fill="var(--lime)"/>

      <polygon class="brand-card brand-card--deep" points="975,583 1178,688 1064,860 832,766" fill="var(--lime-deep)"/>
      <polygon class="brand-card brand-card--mid" points="968,575 1171,680 1057,852 825,758" fill="var(--lime-mid)"/>
      <polygon class="brand-card brand-card--main" points="960,567 1163,672 1050,845 818,750" fill="var(--lime)"/>
    </svg>

    <section class="title-block">
      <h1 class="title-block__heading">PROJECT <span class="title-block__accent">TITLE HERE</span></h1>
      <p class="title-block__subtext">SUBTEXT HERE</p>
    </section>

    <footer class="brand">
      <div class="brand__name">LUMOTEX</div>
      <p class="brand__tagline">YOUR TAGLINE<br>GOES HERE</p>
    </footer>
  </main>
</body>
</html>
```